The Kestrel Personal Training Studio Information Card

The front and back of card to give people that walk in to our gym. There are a few things to say on the card. But it also needs to be designed in an attractive way. You can make some of the information bullett points or with icons or graphics. Please look at our website at https://thekestreltraining.com/ . The card will be 4" x 9"

Target Market(s)

High End Clientele who want to train in a private gym

Industry/Entity Type

Fitness

Font styles to use
Serif
Sans Serif
Other font styles liked:
• the same font Borvale uses on the veltab

Colors
F0912C
F2A743
F7CA91
FBE8D2
FDF5EE

Requirements
Must have
• A cool look

```html
<!DOCTYPE html>
<html lang="en">
<head>
<meta charset="UTF-8">
<title>The Kestrel Private Training Studio – Information Card</title>
<link href="https://fonts.googleapis.com/css2?family=Arimo:wght@400;700&family=Rubik+Dirt&display=swap" rel="stylesheet">
<style>
  :root {
    --bg: #bdbdbd;
    --red: #e8393f;
    --ink: #2a2a2a;
    --ink-deep: #161616;
    --white: #ffffff;
    --logo-grey: #6d6d6d;
    --soft: #e4e4e4;
  }
  * { box-sizing: border-box; margin: 0; padding: 0; }
  html, body { width: 1200px; height: 900px; overflow: hidden; }
  body {
    background: var(--bg);
    font-family: "Arimo", Arial, sans-serif;
    position: relative;
  }
  .card {
    position: absolute;
    top: 60px;
    width: 347px;
    height: 780px;
    overflow: hidden;
    box-shadow: 0 6px 18px rgba(0,0,0,.25);
  }
  .card-front { left: 232px; background: var(--ink); }
  .card-back { left: 621px; background: var(--ink); color: var(--white); }

  /* Front */
  .front-header {
    height: 112px;
    background: var(--white);
    display: flex;
    flex-direction: column;
    align-items: center;
    justify-content: center;
  }
  .brand-name {
    font-weight: 700;
    font-size: 34px;
    letter-spacing: 1px;
    color: var(--logo-grey);
    text-transform: uppercase;
    line-height: 1;
  }
  .brand-tagline {
    font-weight: 700;
    font-size: 9.5px;
    letter-spacing: 3px;
    color: var(--logo-grey);
    text-transform: uppercase;
    margin-top: 6px;
  }
  .front-photo {
    position: absolute;
    top: 112px; left: 0;
    width: 100%; height: 550px;
    background:
      radial-gradient(ellipse at 70% 70%, #3a3633 0%, transparent 60%),
      linear-gradient(180deg, #3b3431 0%, #2a2624 35%, #1c1a19 70%, #2b2523 100%);
  }
  .front-content {
    position: absolute;
    top: 140px; left: 30px; right: 24px;
  }
  .quote-mark {
    font-family: "Rubik Dirt", "Arimo", sans-serif;
    color: var(--red);
    font-size: 60px;
    line-height: .6;
    height: 32px;
  }
  .headline {
    font-family: "Rubik Dirt", "Arimo", sans-serif;
    color: var(--white);
    font-size: 29px;
    line-height: 1.08;
    text-transform: uppercase;
    margin-top: 6px;
  }
  .goal-list {
    list-style: none;
    margin-top: 36px;
    display: grid;
    grid-template-columns: 1fr 1fr;
    row-gap: 26px;
    column-gap: 10px;
  }
  .goal {
    display: flex;
    align-items: center;
    gap: 10px;
    color: var(--white);
    font-size: 13px;
    line-height: 1.2;
  }
  .goal svg { width: 30px; height: 30px; flex: none; }
  .goal-wide { grid-column: 1 / span 2; padding-left: 40px; }
  .front-contact {
    position: absolute;
    bottom: 0; left: 0;
    width: 100%; height: 118px;
    background: var(--red);
    color: var(--white);
    font-weight: 700;
    text-align: center;
    display: flex;
    flex-direction: column;
    justify-content: center;
    gap: 4px;
  }
  .contact-phone { font-size: 24px; letter-spacing: .5px; }
  .contact-web { font-size: 24px; letter-spacing: .3px; }

  /* Back */
  .back-inner { padding: 44px 30px 0 30px; }
  .section-title {
    font-family: "Rubik Dirt", "Arimo", sans-serif;
    color: var(--red);
    font-size: 31px;
    line-height: 1.05;
    text-transform: uppercase;
  }
  .intro-text {
    font-size: 10.5px;
    line-height: 1.35;
    color: var(--soft);
    margin-top: 18px;
  }
  .intro-text + .intro-text { margin-top: 14px; }
  .divider {
    display: flex;
    align-items: center;
    gap: 10px;
    margin: 26px 0 16px;
  }
  .divider::before, .divider::after {
    content: "";
    flex: 1;
    height: 1px;
    background: var(--soft);
    opacity: .7;
  }
  .divider svg { width: 34px; height: 16px; }
  .rates-title { text-align: center; }
  .rates-sub {
    font-weight: 700;
    font-size: 13px;
    text-transform: uppercase;
    text-align: center;
    margin-top: 4px;
  }
  .rate-list {
    list-style: none;
    display: flex;
    gap: 8px;
    margin-top: 18px;
  }
  .rate {
    flex: 1;
    border: 1.5px solid var(--white);
    border-radius: 9px;
    text-align: center;
    padding: 10px 4px 9px;
  }
  .rate-frequency {
    font-weight: 700;
    font-size: 11px;
    text-transform: uppercase;
    line-height: 1.15;
  }
  .rate-price {
    font-family: "Rubik Dirt", "Arimo", sans-serif;
    color: var(--red);
    font-size: 30px;
    line-height: 1.1;
    margin-top: 4px;
  }
  .rate-unit {
    font-weight: 700;
    font-size: 8px;
    text-transform: uppercase;
  }
  .partner-note {
    display: flex;
    align-items: center;
    justify-content: center;
    gap: 7px;
    font-weight: 700;
    font-size: 12px;
    text-transform: uppercase;
    margin-top: 16px;
  }
  .partner-note .bar {
    width: 4px; height: 15px;
    background: var(--red);
    box-shadow: 6px 0 0 var(--red);
  }
  .partner-note .bar-end { box-shadow: -6px 0 0 var(--red); }
  .partner-example {
    font-size: 10.5px;
    line-height: 1.35;
    color: var(--soft);
    text-align: center;
    margin-top: 10px;
  }
</style>
</head>
<body>

<section class="card card-front" aria-label="Card front">
  <header class="front-header">
    <div class="brand-name">The Kestrel</div>
    <div class="brand-tagline">Private Training Studio</div>
  </header>

  <div class="front-photo" role="img" aria-label="Dim gym floor with barbell plates and battle ropes"></div>

  <div class="front-content">
    <div class="quote-mark">&ldquo;</div>
    <h1 class="headline">A safe an individualized approach to strength training.</h1>

    <ul class="goal-list">
      <li class="goal">
        <svg viewBox="0 0 30 30" fill="none" stroke="#e8393f" stroke-width="2.2" stroke-linecap="round"><line x1="4" y1="9" x2="26" y2="9"/><line x1="6" y1="5" x2="6" y2="13"/><line x1="24" y1="5" x2="24" y2="13"/><circle cx="15" cy="14" r="2.5"/><line x1="15" y1="17" x2="15" y2="23"/><line x1="15" y1="23" x2="10" y2="28"/><line x1="15" y1="23" x2="20" y2="28"/></svg>
        <span>Build<br>strength</span>
      </li>
      <li class="goal">
        <svg viewBox="0 0 30 30" fill="none" stroke="#e8393f" stroke-width="2.2" stroke-linecap="round"><circle cx="13" cy="7" r="3"/><path d="M5 22c3-8 13-8 18-3"/><line x1="3" y1="26" x2="27" y2="26"/></svg>
        <span>Increase<br>Flexibility</span>
      </li>
      <li class="goal">
        <svg viewBox="0 0 30 30" fill="none" stroke="#e8393f" stroke-width="2.2" stroke-linecap="round"><rect x="9" y="7" width="12" height="16" rx="3"/><line x1="12" y1="3" x2="18" y2="3"/><line x1="12" y1="27" x2="18" y2="27"/><line x1="15" y1="11" x2="15" y2="15"/><line x1="15" y1="15" x2="18" y2="17"/></svg>
        <span>Train for<br>an event</span>
      </li>
      <li class="goal">
        <svg viewBox="0 0 30 30" fill="none" stroke="#e8393f" stroke-width="2.2" stroke-linecap="round"><rect x="3" y="5" width="18" height="20" rx="3"/><circle cx="12" cy="16" r="4"/><line x1="26" y1="7" x2="26" y2="20"/><polyline points="23,17 26,21 29,17"/></svg>
        <span>Weight<br>Loss</span>
      </li>
      <li class="goal goal-wide">
        <svg viewBox="0 0 30 30" fill="none" stroke="#e8393f" stroke-width="2.2" stroke-linecap="round"><path d="M8 8l2 10h12c3 0 5 2 5 5H6"/><line x1="1" y1="13" x2="6" y2="13"/><line x1="2" y1="18" x2="7" y2="18"/><line x1="12" y1="12" x2="16" y2="12"/></svg>
        <span>Improve functional<br>&amp; daily movements,</span>
      </li>
    </ul>
  </div>

  <footer class="front-contact">
    <div class="contact-phone">0123 456 7811</div>
    <div class="contact-web">WWW.THEKESTREL.COM</div>
  </footer>
</section>

<section class="card card-back" aria-label="Card back">
  <div class="back-inner">
    <h2 class="section-title">How do you<br>get started?</h2>

    <p class="intro-text">We schedule prospective clients for a no cost or obligation consultation. At that consultation we will do a movement screen with you. This will allow the trainer to see what level of flexibility and strength you are currently at. You will be able to discuss your goals and other issues (injuries, etc) at that time.</p>
    <p class="intro-text">Our clients have different goals: Build strength, Increase Flexibility, Improve functional and daily movements, Train for an event, or Weight Loss. We will tailor your training program to the specific results you are looking for.</p>
    <p class="intro-text">Some ways of training increase the chance of injury, we do not practice those types of training at The Kestrel. Many of our clients have current or past injuries that can cause problems. We work with them to not aggravate those injuries or allow them to become an obstacle to their workouts.</p>

    <div class="divider">
      <svg viewBox="0 0 34 16" fill="#ffffff"><rect x="2" y="3" width="4" height="10"/><rect x="7" y="1" width="4" height="14"/><rect x="11" y="7" width="12" height="2"/><rect x="23" y="1" width="4" height="14"/><rect x="28" y="3" width="4" height="10"/></svg>
    </div>

    <h2 class="section-title rates-title">Our rates</h2>
    <p class="rates-sub">All sessions are 60 minutes</p>

    <ul class="rate-list">
      <li class="rate">
        <div class="rate-frequency">1 time<br>per week</div>
        <div class="rate-price">$110</div>
        <div class="rate-unit">Per session</div>
      </li>
      <li class="rate">
        <div class="rate-frequency">2 times<br>per week</div>
        <div class="rate-price">$85</div>
        <div class="rate-unit">Per session</div>
      </li>
      <li class="rate">
        <div class="rate-frequency">3 times<br>per week</div>
        <div class="rate-price">$80</div>
        <div class="rate-unit">Per session</div>
      </li>
    </ul>

    <p class="partner-note"><span class="bar"></span><span>&nbsp;Add $40 for a partnered session&nbsp;</span><span class="bar bar-end"></span></p>
    <p class="partner-example">Example: A Partnered Session (2 people training together) coming twice a week is $125 per session</p>
  </div>
</section>

</body>
</html>
```